Korvel CD Cover Design Project

I need a CD front cover(front inlay) , CD top artwork, CD back cover (back inlay)
i have provided a picture and other
Artiste Name: Korvel
Song Title: Tolulope (carry me Away)
Producer: Rinzo
Track-list
1. Tolulope (carry me Away)
2. Tolulope (carry me Away) acapella
3. Tolulope (carry me Away) (Instrumental)
stay connected:
flitterpost.example/markorvel
circlepage.example/markorvel
www.korvelmusic.example
Management contact:
USA : Verity @ +12125550148 / verity@quillstonemedia.example
UK: Orla @ +447700900412/ +447700900786 / orlatunes@mailbox.example
Nigeria: Ngozi @ +2348000000193 / ngozi@korvelmusic.example
Target Market(s)
african Music consumers globally
Industry/Entity Type
Management
Look and feel
Each slider illustrates characteristics of the customer's brand and the style your logo design should communicate.

```html
<!DOCTYPE html>
<html lang="en">
<head>
<meta charset="utf-8">
<title>Korvel – Tolulope (carry me Away) disc label</title>
<link rel="stylesheet" href="https://fonts.googleapis.com/css2?family=Courgette&family=Abril+Fatface&display=swap">
<style>
  :root {
    --page: #ffffff;
    --ink: #111111;
    --ink-soft: #1c1c1c;
    --panel: rgba(255, 255, 255, 0.72);
    --hub: #f7f7f7;
    --hub-ring: #cfcfcf;
    --hole-edge: #bdbdbd;
    --social: #3b6fb0;
    --sky: #e9ecea;
    --sky-blue: #b8cfd9;
    --sea-deep: #1f5f85;
    --sea: #2a9cb5;
    --surf: #9cc8cf;
    --sand-light: #e2ddcf;
    --sand: #d6c6a6;
    --sand-deep: #c6b18d;
  }
  * { box-sizing: border-box; margin: 0; padding: 0; }
  html, body { width: 1200px; height: 960px; overflow: hidden; background: var(--page); }

  .canvas { position: relative; width: 1200px; height: 960px; background: var(--page); }

  .disc {
    position: absolute; left: 185px; top: 55px;
    width: 840px; height: 840px; border-radius: 50%;
    overflow: hidden;
  }
  .disc__artwork {
    position: absolute; inset: 0;
    background: linear-gradient(180deg,
      var(--sky) 0%, var(--sky-blue) 21%, var(--sea-deep) 23%,
      var(--sea) 30%, var(--surf) 44%, var(--sand-light) 55%,
      var(--sand) 72%, var(--sand-deep) 100%);
  }

  .artist-name {
    position: absolute; left: 0; right: 0; top: 68px;
    text-align: center;
    font-family: "Abril Fatface", serif;
    font-weight: 400;
    font-size: 74px; line-height: 1; letter-spacing: 8px;
    color: var(--ink);
  }

  .contact-panel {
    position: absolute; left: 0; top: 263px;
    width: 335px; height: 297px;
    background: var(--panel);
  }
  .contact {
    position: absolute; left: 0; top: 272px; width: 250px;
    text-align: center;
    font-family: "Courgette", cursive;
    font-size: 13.5px; line-height: 16.5px;
    color: var(--ink-soft);
  }
  .contact__heading { margin-bottom: 5px; }
  .contact__region { margin-top: 5px; }

  .connect {
    position: absolute; left: 43px; top: 490px; width: 280px;
    font-family: "Courgette", cursive;
    font-size: 13px; line-height: 16px;
    color: var(--ink-soft);
  }
  .connect__line { padding-left: 3px; display: flex; align-items: center; gap: 6px; }
  .connect__line--web { padding-left: 24px; }
  .connect__mark { width: 11px; height: 11px; background: var(--social); flex: none; }

  .hub {
    position: absolute; left: 50%; top: 50%;
    width: 280px; height: 280px; margin: -140px 0 0 -140px;
  }

  .song-title {
    position: absolute; left: 140px; top: 626px; width: 430px;
    text-align: center;
    font-family: "Abril Fatface", serif;
    font-size: 84px; line-height: 1;
    color: var(--ink);
    text-shadow: 0 0 2px #fff, 0 0 5px #fff;
  }
  .song-subtitle {
    position: absolute; left: 236px; top: 704px; width: 410px;
    text-align: center;
    font-family: "Abril Fatface", serif;
    font-size: 42px; line-height: 1;
    color: var(--ink);
    text-shadow: 0 0 2px #fff, 0 0 5px #fff;
  }
</style>
</head>
<body>
<main class="canvas">
  <section class="disc">
    <div class="disc__artwork" role="img" aria-label="Beach photograph with sky, sea and sand, overlaid with a sketched portrait of the artist in sunglasses"></div>

    <h1 class="artist-name">KORVEL</h1>

    <div class="contact-panel"></div>
    <div class="contact">
      <p class="contact__heading">Management contact:-</p>
      <p>USA :</p>
      <p>Verity @ +12125550148</p>
      <p>verity@quillstonemedia.example</p>
      <p class="contact__region">UK :</p>
      <p>Orla @ +447700900412/</p>
      <p>+447700900786</p>
      <p>orlatunes@mailbox.example</p>
      <p class="contact__region">Nigeria :</p>
      <p>Ngozi @ +2348000000193</p>
      <p>ngozi@korvelmusic.example</p>
    </div>

    <div class="connect">
      <p>stay connected:</p>
      <p class="connect__line connect__line--web">www.korvelmusic.example</p>
      <p class="connect__line"><span class="connect__mark"></span>flitterpost.example/markorvel</p>
      <p class="connect__line"><span class="connect__mark"></span>circlepage.example/markorvel</p>
    </div>

    <svg class="hub" viewBox="0 0 280 280" aria-hidden="true">
      <circle cx="140" cy="140" r="138" fill="var(--hub)" stroke="var(--hub-ring)" stroke-width="4"/>
      <circle cx="140" cy="140" r="120" fill="none" stroke="var(--hub-ring)" stroke-width="1.5"/>
      <circle cx="140" cy="140" r="55" fill="var(--page)" stroke="var(--hole-edge)" stroke-width="2"/>
    </svg>

    <p class="song-title">Tolulope</p>
    <p class="song-subtitle">(carry me Away)</p>
  </section>
</main>
</body>
</html>
```